Candle Rental Business seeks new website design

We need a new website design for a Candle hire business. The business rents out pillar candles for events such as weddings and corporate events. Our main target market is weddings. The business name is Hire a Lantern. The business name does not have a logo design.

We would like a website that is light in colours and creates a warm atmosphere. The design needs to be elegant and upmarket. There are different size candles that we hire out, ranging from 10cm diameter to 20cm diameter, flat, tall etc. All our candles are white in colour. Its just the size that differs.

We would also like to include a section for hiring out decor such as glassvases, candlebras, overlays and chairs sachets, chair covers. However, this is not the businesses main focus but an additional offering to customers.

Target Market(s)

Wedding venues and brides. Corporate events. School dances.

Industry/Entity Type

Hospitality

Logo Text

Hire a Lantern

Number of Pages Required

1 page

Font styles to use
Sans Serif
Script

Requirements
Must have
• Pictures of pillar candles. Plain white candles. The website must centre around candles.
Nice to have
• Different examples of candle centrepieces
Should not have
• Pictures must not be of brides. Pictures of surrounding is perferable.

```html
<!DOCTYPE html>
<html lang="en">
<head>
<meta charset="utf-8">
<title>Hire a Lantern</title>
<link href="https://fonts.googleapis.com/css2?family=Kaushan+Script&family=Roboto:wght@300;400;500&display=swap" rel="stylesheet">
<style>
:root{
  --gold:#e0aa2e;
  --rust:#c9582b;
  --footer:#c45d2a;
  --green:#8ca53b;
  --cream:#f5f1e8;
  --text:#6b6b6b;
  --dark:#3d3d3d;
  --white:#ffffff;
}
*{margin:0;padding:0;box-sizing:border-box}
html,body{width:768px;height:1200px;overflow:hidden;background:var(--white)}
body{position:relative;font-family:"Roboto",Arial,sans-serif;color:var(--text)}
.abs{position:absolute}

/* hero */
.hero{left:0;top:0;width:768px;height:349px;
  background:
    radial-gradient(ellipse 60px 80px at 118px 190px,rgba(255,230,140,.95),rgba(240,170,60,.55) 55%,transparent 100%),
    radial-gradient(ellipse 40px 50px at 200px 300px,rgba(255,220,120,.8),transparent 100%),
    radial-gradient(ellipse 70px 60px at 455px 255px,rgba(220,70,40,.85),rgba(140,30,25,.5) 60%,transparent 100%),
    radial-gradient(ellipse 160px 90px at 100px 250px,rgba(190,140,80,.55),transparent 100%),
    radial-gradient(ellipse 120px 120px at 680px 180px,rgba(120,60,50,.5),transparent 100%),
    linear-gradient(160deg,#5a1c16 0%,#7a2a1e 40%,#5e1d18 70%,#3a110d 100%)}
.nav{left:84px;top:0;width:600px;height:42px;background:var(--gold);font-size:10.5px;color:var(--white)}
.nav a{position:absolute;top:14px;color:var(--white);text-decoration:none;transform:translateX(-50%);white-space:nowrap}
.brand{left:296px;top:0;width:160px;height:81px;background:var(--white);border-radius:0 0 80px 80px / 0 0 44px 44px;display:flex;align-items:center;justify-content:center;gap:6px;font-size:15px;color:var(--rust);padding-top:0}
.brand .dot{width:9px;height:9px;border-radius:50%;background:var(--gold)}
.tagline{left:0;top:157px;width:768px;text-align:center;font-family:"Kaushan Script",cursive;font-weight:400;font-size:32px;color:var(--white);text-shadow:0 2px 6px rgba(0,0,0,.4)}
.thumb{top:280px;width:86px;height:45px;border:2px solid var(--white)}
.pointer{left:279px;top:274px;width:0;height:0;border-left:6px solid transparent;border-right:6px solid transparent;border-bottom:6px solid var(--white)}

/* headings */
.section-title{font-weight:400;color:var(--dark);font-size:16px;line-height:20px}
.section-title span{color:var(--rust)}
.leaf{display:inline-block;width:9px;height:13px;background:var(--green);border-radius:0 9px 0 9px;vertical-align:-1px;margin:0 12px}

.about h2{left:0;top:373px;width:768px;text-align:center}
.about p{left:84px;top:406px;width:600px;text-align:center;font-size:8.8px;line-height:15.6px;font-weight:300}

/* services */
.band{left:0;top:484px;width:768px;height:338px;background:var(--cream)}
.card{background:var(--white)}
.card h3{font-weight:400;color:var(--rust);font-size:16px;line-height:20px}
.card p{font-size:7.6px;line-height:13.2px;font-weight:300}
.btn{display:block;background:var(--green);color:var(--white);font-size:7.6px;line-height:17px;height:17px;width:59px;text-align:center}
.photo{position:absolute}

/* gallery */
.gallery h2{left:84px;top:844px}
.gallery h2 .leaf{margin:0 0 0 6px}
.gimg{width:127px;height:71px}
.quote{left:524px;top:857px;width:160px;height:175px;background:var(--gold);text-align:center;color:var(--white)}
.avatar{left:578px;top:845px;width:52px;height:52px;border-radius:50%;background:radial-gradient(circle at 50% 40%,#e8d6c0,#9c7650);border:2px solid var(--white)}
.quote p{position:absolute;left:12px;top:50px;width:136px;font-size:7.6px;line-height:13.2px;font-weight:300}
.quote .who{top:133px;font-size:9px;line-height:14px;color:var(--rust);font-weight:500}
.dots{position:absolute;left:51px;top:160px;display:flex;gap:3px}
.dots i{display:block;width:17px;height:2px;background:rgba(255,255,255,.45)}
.dots i:first-child{background:var(--white)}

/* footer */
.footer{left:0;top:1057px;width:768px;height:143px;background:var(--footer);color:var(--white)}
.footer h4{position:absolute;font-weight:400;color:var(--gold);font-size:12px;line-height:16px}
.footer .small{font-size:8.8px;line-height:13.4px}
.social{position:absolute;top:1103px;width:19px;height:19px;background:rgba(255,255,255,.28);border:1px solid rgba(255,255,255,.5)}
.rule{left:84px;top:1142px;width:600px;height:1px;background:rgba(255,255,255,.3)}
.flinks{left:0;top:1156px;width:768px;text-align:center;font-size:8.8px;line-height:12px;color:var(--white)}
.flinks b{font-weight:400;margin:0 5px}
.copy{left:0;top:1173px;width:768px;text-align:center;font-size:8.8px;line-height:12px;color:var(--white)}
</style>
</head>
<body>
<header>
  <div class="abs hero" role="img" aria-label="Candlelit table setting with glassware and a red mosaic votive"></div>
  <nav class="abs nav">
    <a style="left:37px">Home</a><a style="left:102px">About Us</a><a style="left:173px">Services</a>
    <a style="left:414px">Products</a><a style="left:481px">Gallery</a><a style="left:553px">Contact Us</a>
  </nav>
  <div class="abs brand"><span class="dot"></span>Hire a Lantern</div>
  <h1 class="abs tagline">Meaningful gift at a friendly price point</h1>
  <div class="abs pointer"></div>
  <div class="abs thumb" style="left:242px;background:radial-gradient(ellipse at 30% 60%,#f3c462,#9a3a22 55%,#4a1812)" role="img" aria-label="Candles beside a red votive"></div>
  <div class="abs thumb" style="left:342px;background:radial-gradient(ellipse at 50% 55%,#f0d08a,#8a5a2a 50%,#2e1c10)" role="img" aria-label="Row of pillar candles"></div>
  <div class="abs thumb" style="left:441px;background:linear-gradient(90deg,#4a3a30,#c9b8a8 60%,#f1ece6)" role="img" aria-label="Candle lighting at a ceremony"></div>
</header>

<section class="about">
  <h2 class="abs section-title"><i class="leaf"></i>About <span>Hire a Lantern</span><i class="leaf"></i></h2>
  <p class="abs">We are a family owned and operated company and began making decorative candles for all occasions. All of our candles are individually hand made in our candle studio, situated in Millbrook, outside Harbourton. Our wax is local and of a very high quality, and dripless! Our wax is also made with a high melting point, which means it will not melt or bend in hot temperatures.</p>
</section>

<section class="abs band"></section>
<article class="abs card" style="left:84px;top:509px;width:225px;height:295px">
  <div class="photo" style="left:12px;top:10px;width:201px;height:120px;background:radial-gradient(ellipse 50px 60px at 50% 45%,#ffffff,#eeeae4 60%,transparent 100%),linear-gradient(180deg,#b8a98e 0%,#dcd6cc 45%,#c9d2d4 75%,#6fb0c4 100%)" role="img" aria-label="White pillar candles with glassware on a table"></div>
  <h3 class="abs" style="left:12px;top:143px">Hire Candles</h3>
  <p class="abs" style="left:12px;top:167px;width:203px">Do you love using candles for your events but tired of sorting old used candles or buying expensive candles. Believe it or not you can now rent candles.All our candles come in different sizes and heights.You can add the ambience of candlelight to your event of wedding ceremony without the worry over dripping wax or open candle flames.</p>
  <span class="abs btn" style="left:12px;top:266px">Read More</span>
</article>
<article class="abs card" style="left:321px;top:509px;width:363px;height:141px">
  <h3 class="abs" style="left:12px;top:7px">Personalised Candles</h3>
  <p class="abs" style="left:12px;top:35px;width:208px">Hire a Lantern provides the opportunity to give a thoughtful, meaningful gift at a friendly price point. This unique gift conveys the time and care you put into creating it. The recipient will enjoy the beautiful presentation and be reminded of the sentiment...</p>
  <span class="abs btn" style="left:12px;top:112px">Read More</span>
  <div class="photo" style="left:229px;top:10px;width:124px;height:123px;background:radial-gradient(ellipse 30px 40px at 35% 50%,#e88ab0,transparent 100%),radial-gradient(ellipse 32px 42px at 68% 62%,#f4ead8,transparent 100%),linear-gradient(180deg,#b9bfc5,#e4e2de)" role="img" aria-label="Personalised candles in glass jars"></div>
</article>
<article class="abs card" style="left:321px;top:663px;width:363px;height:141px">
  <h3 class="abs" style="left:12px;top:7px">Décor Hire</h3>
  <p class="abs" style="left:12px;top:35px;width:212px">We hire a selection of overlays, chair sachets and chair covers as well as glassware and candelabras to compliment your decor.</p>
  <span class="abs btn" style="left:12px;top:85px">Read More</span>
  <div class="photo" style="left:232px;top:11px;width:120px;height:119px;background:radial-gradient(ellipse 14px 18px at 50% 45%,#ffe7a0,transparent 100%),radial-gradient(ellipse 60px 28px at 50% 72%,#e8ecc0,#5e7a2e 60%,transparent 100%),linear-gradient(180deg,#6a2a20 0%,#8a3c2c 40%,#d8d6cc 100%)" role="img" aria-label="Floral centrepiece with a candle and wine glasses"></div>
</article>

<section class="gallery">
  <h2 class="abs section-title">Our <span>Photo Gallery</span><i class="leaf"></i></h2>
  <div class="abs gimg" style="left:84px;top:878px;background:radial-gradient(ellipse at 35% 40%,#f4d8a8,#b88a5a 50%,#8a6a4a)" role="img" aria-label="Candlesticks and flowers on a table"></div>
  <div class="abs gimg" style="left:223px;top:878px;background:radial-gradient(ellipse at 45% 75%,#f0b060,#2a6ea0 45%,#163e66)" role="img" aria-label="Blue lit reception with candles"></div>
  <div class="abs gimg" style="left:362px;top:878px;background:radial-gradient(ellipse at 40% 45%,#fbe2a0,#a7783a 40%,#2e2010)" role="img" aria-label="Candle glowing in the dark"></div>
  <div class="abs gimg" style="left:84px;top:962px;background:radial-gradient(ellipse at 45% 40%,#fae0a4,#9a6228 45%,#24160c)" role="img" aria-label="Tall taper candles"></div>
  <div class="abs gimg" style="left:223px;top:962px;background:radial-gradient(ellipse at 50% 70%,#f2d0a8,#a26a3a 45%,#22140e)" role="img" aria-label="Candlelit table with white roses"></div>
  <div class="abs gimg" style="left:362px;top:962px;background:radial-gradient(ellipse at 55% 50%,#ffffff,#d8ccc0 40%,#5a4a3e)" role="img" aria-label="Candles lit in a venue"></div>
</section>
<aside class="abs quote">
  <p>“There are many variations of passages of Lorem Ipsum available, but the majority have suffered alteration in some form, by injected humour, or randomised words which don't look even slightly believable.”</p>
  <p class="who">Marcus Ellery</p>
  <div class="dots"><i></i><i></i><i></i></div>
</aside>
<div class="abs avatar" role="img" aria-label="Client portrait"></div>

<footer class="abs footer">
  <h4 style="left:85px;top:21px">Location</h4>
  <p class="abs small" style="left:85px;top:40px">Simply dummy text printing<br>typesetting AT 12356</p>
  <p class="abs" style="left:0;top:28px;width:768px;text-align:center;font-size:11.5px;line-height:16px;color:var(--gold)">+123 555 0190</p>
  <p class="abs" style="left:0;top:45px;width:768px;text-align:center;font-size:12px;line-height:16px;font-weight:500">info@hirealantern-events.com</p>
  <h4 style="right:84px;top:21px">Follow us</h4>
</footer>
<div class="abs social" style="left:585px" aria-label="Social link"></div>
<div class="abs social" style="left:612px" aria-label="Social link"></div>
<div class="abs social" style="left:638px" aria-label="Social link"></div>
<div class="abs social" style="left:665px" aria-label="Social link"></div>
<div class="abs rule"></div>
<p class="abs flinks">Home<b>I</b>About Us<b>I</b>Services<b>I</b>Products<b>I</b>Gallery<b>I</b>Contact Us</p>
<p class="abs copy">© 2016 Hire a Lantern, All Rights Reserved</p>
</body>
</html>
```